Service Menu refresh 2018 Update of menu pricing

We currently have service menus as attached. We will be updating our look via our homepage image, our service menu and our in-house beverage and treatment menu.
We are a natural and sustainable hair salon group and moving more towards head spa which consists of treatments, beauty, tanning as well as your traditional hair services. Our imagery needs to reflect our efforts in spa treatments in the hair and scalp area and use natural materials and colours reflecting sustainability.
Velune is the brand we stock and promote.

Target Market(s)

Men or women interesting in personal maintenance with natural and organic products and using sustainable practises

Industry/Entity Type

Hair And Beauty

Font styles to use
Sans Serif
Other font styles liked:
• Arial or Helvetica

Colors
9acb3c
abd037
cadf82
ffffff

Requirements
Must have
• Name on the front cover, locations on back cover
Nice to have
• Prestige feel, reflect male and female clients
Should not have
• Bold artificial writing or any type of cartoon images.
• Same images as existing menu.

```html
<!DOCTYPE html>
<html lang="en">
<head>
<meta charset="utf-8">
<title>Verdant Roots hair studios – Service Menu</title>
<link rel="stylesheet" href="https://fonts.googleapis.com/css2?family=Arimo:wght@400;700&display=swap">
<style>
  :root {
    --green: #9acb3c;
    --green-lime: #abd037;
    --green-pale: #cadf82;
    --white: #ffffff;
    --ink: #2b2b2b;
    --ink-soft: #555555;
    --header-grey: #5c5c5c;
    --cell-grey: #ececec;
    --line-grey: #d6d6d6;
    --stage: #e9eaec;
  }
  * { box-sizing: border-box; margin: 0; padding: 0; }
  html, body { width: 807px; height: 1200px; overflow: hidden; }
  body {
    background: var(--stage);
    font-family: "Arimo", Arial, Helvetica, sans-serif;
    color: var(--ink);
    position: relative;
  }
  .page {
    position: absolute;
    background: var(--white);
    box-shadow: 0 2px 8px rgba(0,0,0,.12);
    overflow: hidden;
  }

  /* ---------- Back cover ---------- */
  .back-cover { left: 30px; top: 60px; width: 360px; height: 360px; padding: 26px 26px 20px; }
  .philosophy { font-size: 15.5px; font-weight: 700; line-height: 1.22; margin-bottom: 14px; }
  .location { margin-bottom: 7px; }
  .location-name { color: var(--green); font-weight: 700; font-size: 9.5px; text-transform: uppercase; letter-spacing: .2px; }
  .contact-line { display: flex; align-items: center; gap: 5px; font-size: 8.6px; line-height: 1.3; color: var(--ink-soft); }
  .contact-line svg { width: 8px; height: 8px; flex: none; fill: var(--green); }
  .website { color: var(--green); font-weight: 700; font-size: 13.5px; letter-spacing: .6px; margin-top: 10px; }

  /* ---------- Front cover ---------- */
  .front-cover { left: 417px; top: 60px; width: 360px; height: 360px; }
  .foliage {
    position: absolute; right: 0; top: 0; width: 300px; height: 270px;
    background: radial-gradient(ellipse at 65% 35%, #b7dc6a 0%, #cfe79b 35%, #eef6dd 65%, rgba(255,255,255,0) 80%);
  }
  .speckle-field {
    position: absolute; left: 0; top: 110px; width: 300px; height: 250px;
    background: radial-gradient(ellipse at 40% 60%, #e4e4e4 0%, rgba(255,255,255,0) 70%);
  }
  .brand-name {
    position: absolute; left: 118px; top: 120px;
    display: flex; align-items: center; gap: 8px;
    font-size: 19px; font-weight: 700; color: var(--ink);
  }
  .brand-dot { width: 12px; height: 12px; border-radius: 50%; background: var(--green); }

  /* ---------- Inner spread ---------- */
  .spread { left: 30px; top: 470px; width: 747px; height: 373px; display: flex; }
  .spread-page { width: 50%; height: 100%; padding: 22px 20px; position: relative; }
  .spread-page + .spread-page { border-left: 1px solid var(--line-grey); }

  .price-table { width: 100%; border-collapse: collapse; font-size: 8.5px; }
  .price-table th, .price-table td { padding: 2.5px 4px; }
  .col-heads th { background: var(--header-grey); color: var(--white); font-weight: 700; font-size: 9px; text-align: center; }
  .col-heads th.blank { background: transparent; }
  .section-band td {
    background: var(--green-pale); color: var(--ink); font-weight: 700;
    font-size: 11px; text-transform: uppercase; padding: 4px 6px;
  }
  .service { font-weight: 700; text-transform: uppercase; width: 46%; }
  .service.sub { font-weight: 400; text-transform: none; padding-left: 10px; }
  .price { background: var(--cell-grey); text-align: center; width: 13.5%; border-left: 2px solid var(--white); }
  .row td { border-bottom: 2px solid var(--white); }
  .note { font-size: 7px; color: var(--ink-soft); line-height: 1.35; padding-left: 6px; }
  .footnote { position: absolute; left: 20px; right: 20px; bottom: 18px; font-size: 7.5px; color: var(--ink-soft); line-height: 1.5; }
</style>
</head>
<body>

<svg width="0" height="0" style="position:absolute" aria-hidden="true">
  <symbol id="icon-pin" viewBox="0 0 10 10"><path d="M5 0a3.4 3.4 0 0 0-3.4 3.4C1.6 6 5 10 5 10s3.4-4 3.4-6.6A3.4 3.4 0 0 0 5 0zm0 4.8a1.4 1.4 0 1 1 0-2.8 1.4 1.4 0 0 1 0 2.8z"/></symbol>
  <symbol id="icon-phone" viewBox="0 0 10 10"><path d="M2 0.5l1.8 2.2-1 1.2a6 6 0 0 0 3.3 3.3l1.2-1L9.5 8 8 9.5C4 9.5.5 6 .5 2z"/></symbol>
  <symbol id="icon-mail" viewBox="0 0 10 10"><path d="M0 2h10v6H0zm1 .8v.3l4 2.5 4-2.5v-.3z"/></symbol>
</svg>

<!-- Back cover -->
<section class="page back-cover">
  <p class="philosophy">“Living a more natural and organic life is a philosophy not just a product certification”</p>

  <div class="location">
    <p class="location-name">Ashgrove</p>
    <p class="contact-line"><svg><use href="#icon-pin"/></svg>Shop 12 Ashgrove Village, Kerr Lane, Ashgrove</p>
    <p class="contact-line"><svg><use href="#icon-phone"/></svg>+61 (07) 5550 1401</p>
    <p class="contact-line"><svg><use href="#icon-mail"/></svg>ashgrove@verdantroots.com.au</p>
  </div>
  <div class="location">
    <p class="location-name">Kelvin Grove</p>
    <p class="contact-line"><svg><use href="#icon-pin"/></svg>Shop 48 Grove Plaza, Fern Road, Kelvin Grove</p>
    <p class="contact-line"><svg><use href="#icon-phone"/></svg>+61 (07) 5550 2276</p>
    <p class="contact-line"><svg><use href="#icon-mail"/></svg>kelvingrove@verdantroots.com.au</p>
  </div>
  <div class="location">
    <p class="location-name">In Milton</p>
    <p class="contact-line"><svg><use href="#icon-pin"/></svg>Shop 7 Milton Arcade, Park Road, Milton</p>
    <p class="contact-line"><svg><use href="#icon-phone"/></svg>+61 (07) 5550 3318</p>
    <p class="contact-line"><svg><use href="#icon-mail"/></svg>milton@verdantroots.com.au</p>
  </div>
  <div class="location">
    <p class="location-name">Redcliffe</p>
    <p class="contact-line"><svg><use href="#icon-pin"/></svg>Shop 21 Bayside Centre, Anzac Ave, Redcliffe</p>
    <p class="contact-line"><svg><use href="#icon-phone"/></svg>+61 (07) 5550 4492</p>
    <p class="contact-line"><svg><use href="#icon-mail"/></svg>redcliffe@verdantroots.com.au</p>
  </div>
  <div class="location">
    <p class="location-name">Riverside Health Centre</p>
    <p class="contact-line"><svg><use href="#icon-pin"/></svg>Willow St, Riverside QLD 4000</p>
    <p class="contact-line"><svg><use href="#icon-phone"/></svg>+61 (07) 5550 5530</p>
    <p class="contact-line"><svg><use href="#icon-mail"/></svg>riverside@verdantroots.com.au</p>
  </div>

  <p class="website">WWW.VERDANTROOTS.COM.AU</p>
</section>

<!-- Front cover -->
<section class="page front-cover">
  <div class="foliage" role="img" aria-label="Photograph of fresh green leaves on a branch, softly lit"></div>
  <div class="speckle-field" role="img" aria-label="Soft grey halftone dot texture"></div>
  <p class="brand-name"><span class="brand-dot"></span>Verdant Roots</p>
</section>

<!-- Inner spread -->
<section class="page spread">
  <div class="spread-page">
    <table class="price-table">
      <tr class="col-heads"><th class="blank"></th><th>S</th><th>M</th><th>L</th><th>XL</th></tr>
      <tr class="section-band"><td colspan="5">Cut &amp; Blowdry</td></tr>
      <tr class="row"><td class="service">Ladies</td><td class="price">$77</td><td class="price">$88</td><td class="price">$99</td><td class="price">$110</td></tr>
      <tr class="row"><td class="service">Fringe</td><td class="price">$15</td><td class="price"></td><td class="price"></td><td class="price"></td></tr>
      <tr class="row"><td class="service sub">Trim</td><td class="price">$45</td><td class="price">$55</td><td class="price">$65</td><td class="price">$75</td></tr>
      <tr class="row"><td class="service sub">Restyle</td><td class="price">$95</td><td class="price">$105</td><td class="price">$115</td><td class="price">$125</td></tr>
      <tr class="section-band"><td colspan="5">Gents &amp; Children</td></tr>
      <tr class="row"><td class="service">Gents cut</td><td class="price">$45</td><td class="price">$55</td><td class="price">$67</td><td class="price">$77</td></tr>
      <tr class="row"><td class="service">Children</td><td class="price">$30</td><td class="price">$35</td><td class="price"></td><td class="price"></td></tr>
      <tr class="section-band"><td colspan="5">Blowdry only</td></tr>
      <tr class="row"><td class="service">Blowdry</td><td class="price">$45</td><td class="price">$55</td><td class="price">$67</td><td class="price">$77</td></tr>
    </table>
  </div>

  <div class="spread-page">
    <table class="price-table">
      <tr class="col-heads"><th class="blank"></th><th>S</th><th>M</th><th>L</th><th>XL</th></tr>
      <tr class="section-band"><td colspan="5">Colour</td></tr>
      <tr class="row"><td class="service">Regrowth</td><td class="price">$83</td><td class="price">$145</td><td class="price">$165</td><td class="price">$185</td></tr>
      <tr class="row"><td class="service">Full colour tint</td><td class="price">$125</td><td class="price">$185</td><td class="price">$209</td><td class="price">$229</td></tr>
      <tr class="row"><td class="service">Regrowth lightening*</td><td class="price">$165</td><td class="price">$275</td><td class="price">$375</td><td class="price">$475</td></tr>
      <tr class="row"><td class="service">Balayage/Ombre*</td><td class="price"></td><td class="price"></td><td class="price">$195</td><td class="price">$205</td></tr>
      <tr class="section-band"><td colspan="5">Bloom</td></tr>
      <tr class="row"><td class="service">Regrowth</td><td class="price">$99</td><td class="price">$175</td><td class="price">$195</td><td class="price">$205</td></tr>
      <tr class="row"><td class="service">Full colour tint</td><td class="price">$155</td><td class="price"></td><td class="price"></td><td class="price"></td></tr>
      <tr class="section-band"><td colspan="5">Foils*</td></tr>
      <tr class="row"><td class="service">Single*</td><td class="price">$11</td><td class="price">$13</td><td class="price">$17</td><td class="price">$22</td></tr>
      <tr class="row"><td class="service">1/4 head</td><td class="price">$135</td><td class="price">$155</td><td class="price">$175</td><td class="price">$195</td></tr>
      <tr class="row"><td class="service">1/2 head</td><td class="price">$185</td><td class="price">$205</td><td class="price">$235</td><td class="price">$265</td></tr>
      <tr class="row"><td class="service">Full head</td><td class="price">$235</td><td class="price">$265</td><td class="price">$315</td><td class="price">$355</td></tr>
      <tr class="section-band"><td colspan="5">Straight</td></tr>
      <tr class="row"><td class="service">Keratin straightening system</td><td class="price">$365</td><td class="price">$445</td><td class="price">$535</td><td class="price">$565</td></tr>
    </table>
    <p class="note">*Includes colour match &amp; toner<br>*Maximum 6 foils without colour<br>*Minimum charge on a Sunday is $40</p>
  </div>

  <p class="footnote">Time is taken for each service. You will ALWAYS receive a firm price after your consultation.<br>S: to the collarbone | L: to the bra strap | XL: past bra strap</p>
</section>

</body>
</html>
```